Professional Photography Business cards

I need business cards that include my logo which I have uploaded. I run a photography business. I am open to ideas but I would like one side to have my logo and the other side to have my contact info. I don't have a website made but I do own a website domain. I have uploaded 2 different logo color schemes. My business colors are Blue, black , and white.

Business Name
Business Phone Number
Business Email
Business Website address
Instagram

Industry/Entity Type

Professional Photography

Contact Information for Business Card

Phone Number: 916-384-7702 email: info@tlane-studio.example Instagram: @t.lanestudio website doman- www.tlane-studio.example

Requirements
Must have
• I like the idea of a business card with a full black background front and back of card. My colors must include royal blue, black, and white

```html
<!DOCTYPE html>
<html lang="en">
<head>
<meta charset="utf-8">
<title>T. Lane Photography – Business Cards</title>
<link rel="stylesheet" href="https://fonts.googleapis.com/css2?family=Cormorant+Garamond:wght@500&display=swap">
<style>
  :root {
    --backdrop: #b3b1b1;
    --card-black: #000000;
    --card-blue: #2b318a;
    --ink-white: #ffffff;
    --silver: #a9a9a9;
    --shadow: rgba(0, 0, 0, 0.45);
  }
  html, body {
    margin: 0;
    padding: 0;
    width: 1200px;
    height: 1200px;
    overflow: hidden;
    background: var(--backdrop);
    font-family: "Cormorant Garamond", Georgia, serif;
    font-weight: 500;
    color: var(--ink-white);
  }
  .canvas {
    position: relative;
    width: 1200px;
    height: 1200px;
  }
  .card {
    position: absolute;
    width: 702px;
    height: 455px;
    box-shadow: -4px 5px 8px var(--shadow);
  }
  .card--contact {
    left: 204px;
    top: 132px;
    background: var(--card-black);
  }
  .card--brand {
    left: 343px;
    top: 646px;
    background: var(--card-blue);
    display: flex;
    align-items: center;
    justify-content: center;
  }
  .brand {
    display: flex;
    align-items: center;
    gap: 12px;
    white-space: nowrap;
  }
  .brand__mark {
    border: 2px solid var(--ink-white);
    border-radius: 50%;
    flex: none;
  }
  .brand__name {
    line-height: 1;
    letter-spacing: 0.5px;
  }
  .card--contact .brand {
    position: absolute;
    left: 62px;
    top: 72px;
  }
  .card--contact .brand__name { font-size: 34px; }
  .card--contact .brand__mark { width: 30px; height: 30px; }
  .card--brand .brand__name { font-size: 54px; }
  .card--brand .brand__mark { width: 48px; height: 48px; border-width: 3px; }

  .accent-ring {
    position: absolute;
    left: 452px;
    top: 186px;
    width: 116px;
    height: 116px;
    border: 5px solid var(--silver);
    border-radius: 50%;
  }
  .contact-list {
    position: absolute;
    left: 50px;
    top: 216px;
    margin: 0;
    padding: 0;
    list-style: none;
  }
  .contact-list__item {
    display: flex;
    align-items: center;
    height: 22px;
    margin-bottom: 21px;
    font-size: 21px;
    letter-spacing: 0.2px;
  }
  .contact-list__item--phone { font-size: 23px; margin-bottom: 20px; }
  .contact-list__icon {
    width: 20px;
    height: 20px;
    margin-right: 18px;
    flex: none;
  }
  .contact-list__social-square {
    width: 15px;
    height: 15px;
    margin: 0 21px 0 3px;
    border: 1.6px solid var(--ink-white);
    border-radius: 3px;
    flex: none;
  }
</style>
</head>
<body>
<main class="canvas">

  <section class="card card--contact" aria-label="Contact side">
    <div class="brand">
      <span class="brand__name">T. Lane Photography</span>
      <span class="brand__mark"></span>
    </div>

    <div class="accent-ring"></div>

    <ul class="contact-list">
      <li class="contact-list__item contact-list__item--phone">
        <svg class="contact-list__icon" viewBox="0 0 24 24" fill="none" stroke="#fff" stroke-width="1.4" stroke-linejoin="round">
          <path d="M5 3h4l2 5-2.5 1.5a11 11 0 0 0 6 6L16 13l5 2v4a2 2 0 0 1-2 2A16 16 0 0 1 3 5a2 2 0 0 1 2-2z"/>
        </svg>
        <span>916-384-7702</span>
      </li>
      <li class="contact-list__item">
        <span class="contact-list__social-square"></span>
        <span>@t.lanestudio</span>
      </li>
      <li class="contact-list__item">
        <svg class="contact-list__icon" viewBox="0 0 24 24" fill="none" stroke="#fff" stroke-width="1.4">
          <rect x="2" y="5" width="20" height="14"/>
          <path d="M2 5l10 8 10-8M2 19l7-7M22 19l-7-7"/>
        </svg>
        <span>info@tlane-studio.example</span>
      </li>
      <li class="contact-list__item">
        <svg class="contact-list__icon" viewBox="0 0 24 24" fill="none" stroke="#fff" stroke-width="1.4">
          <circle cx="12" cy="12" r="9"/>
          <ellipse cx="12" cy="12" rx="4" ry="9"/>
          <path d="M3 12h18M4.5 7.5h15M4.5 16.5h15"/>
        </svg>
        <span>www.tlane-studio.example</span>
      </li>
    </ul>
  </section>

  <section class="card card--brand" aria-label="Brand side">
    <div class="brand">
      <span class="brand__name">T. Lane Photography</span>
      <span class="brand__mark"></span>
    </div>
  </section>

</main>
</body>
</html>
```